Moden - Mexicali - Flower Shop

brisapetals is looking for a cool web design that has a airy, clean, mexicali feel to it.

See attached images and links for idea of what we mean with the above.

please no templates.

Target Market(s)

Local flower shop in San Diego, California

Industry/Entity Type

Shop

Requirements
Must have
• see. brisapetals.shopnest.example - I did the site and logo...I love the logo - hate the site.

Going for this feel: http://www.platetalk.example/menucraft/archives/verdanos.php

I also attached another site I liked- I just feel like it may be to busy.

```html
<!DOCTYPE html>
<html lang="en">
<head>
<meta charset="utf-8">
<title>Brisa Petals – Online Flower Store</title>
<link href="https://fonts.googleapis.com/css2?family=Oxygen:wght@300;400;700&display=swap" rel="stylesheet">
<style>
  :root{
    --ink:#333333;
    --muted:#777777;
    --line:#d8d8d8;
    --rule:#222222;
    --accent:#6fb3a0;
    --logo:#8cc7b8;
    --white:#ffffff;
    --footer:#3b3b3b;
    --footer-dark:#2c2c2c;
    --footer-text:#e6e6e6;
    --submit:#3aaee0;
  }
  *{box-sizing:border-box;margin:0;padding:0}
  html,body{width:1200px;height:2237px;overflow:hidden;background:var(--white)}
  body{position:relative;font-family:"Oxygen",Arial,sans-serif;color:var(--ink)}
  a{color:inherit;text-decoration:none}

  /* top bar */
  .topbar{position:absolute;left:80px;top:0;width:1033px;height:51px;border-bottom:1px solid #e4e4e4}
  .account-links{position:absolute;left:11px;top:18px;font-size:13px;color:#555}
  .account-links span{margin:0 6px;color:#999}
  .search{position:absolute;left:584px;top:9px;width:260px;height:35px;border:1px solid #dcdcdc;font-size:13px;color:#888;padding:10px 12px}
  .search svg{position:absolute;right:10px;top:9px}
  .cart{position:absolute;left:916px;top:14px;font-size:13px;color:#555;display:flex;align-items:center;gap:10px}

  /* logo */
  .brand{position:absolute;left:0;top:80px;width:1200px;display:flex;justify-content:center;align-items:center;gap:26px;font-weight:300;font-size:48px;letter-spacing:16px;color:var(--logo)}
  .brand-mark{width:54px;height:54px;border-radius:50%;border:2px solid var(--logo)}

  /* navigation */
  .main-nav{position:absolute;left:80px;top:174px;width:1033px;height:60px;border-top:1px solid var(--rule);border-bottom:3px solid var(--rule);display:flex;align-items:center}
  .main-nav a{display:flex;justify-content:center;align-items:center;height:26px;font-size:17px;color:#444;text-transform:uppercase}
  .main-nav a + a{border-left:1px solid #cfcfcf}

  /* hero */
  .hero{position:absolute;left:80px;top:260px;width:1033px;height:486px;overflow:hidden}
  .hero-photo{position:absolute;inset:0;background:
      radial-gradient(ellipse 38% 55% at 72% 55%, #f4d21a 0%, #e8bf18 45%, rgba(232,191,24,0) 75%),
      radial-gradient(ellipse 25% 30% at 58% 20%, #f2d330 0%, rgba(242,211,48,0) 80%),
      radial-gradient(ellipse 20% 40% at 95% 25%, #3f6a2e 0%, rgba(63,106,46,0) 80%),
      linear-gradient(100deg,#5a3b26 0%,#7a543a 40%,#6b4830 70%,#4a3020 100%)}
  .hero-copy{position:absolute;left:0;top:0;width:570px;height:486px;color:var(--white);text-align:center}
  .hero-kicker{position:absolute;top:180px;left:0;width:100%;font-size:16px;letter-spacing:1px;padding-left:180px;text-align:left}
  .hero-divider{position:absolute;top:222px;left:172px;width:226px;height:12px}
  .hero-title{position:absolute;top:250px;left:0;width:566px;font-size:37px;font-weight:700;letter-spacing:-0.5px}
  .hero-text{position:absolute;top:312px;left:40px;width:520px;font-size:14px;line-height:25px}
  .hero-button{position:absolute;top:382px;left:218px;width:134px;height:38px;border:1px solid var(--white);font-size:16px;display:flex;align-items:center;justify-content:center}
  .hero-arrow{position:absolute;top:218px}
  .hero-arrow.prev{left:0}
  .hero-arrow.next{right:0}

  /* welcome */
  .welcome-title{position:absolute;left:80px;top:815px;width:290px;text-align:right;font-size:31px;font-weight:300;line-height:43px;color:#555;text-transform:uppercase}
  .welcome-title em{font-style:normal;color:var(--accent)}
  .welcome-text{position:absolute;left:419px;top:818px;width:694px;font-size:13px;line-height:28px;color:#555}

  /* tabs */
  .tabs{position:absolute;left:80px;top:962px;width:1033px;height:22px;display:flex;align-items:center;gap:0}
  .tabs .rule{height:1px;background:var(--rule);flex:1}
  .tabs .dot{width:7px;height:7px;border-radius:50%;background:var(--rule);margin:0 14px}
  .tabs .tab{font-size:16px;letter-spacing:2px;text-transform:uppercase;color:#333}
  .tabs .tab.inactive{color:#999}

  .pager{position:absolute;left:532px;top:1012px;display:flex;gap:8px}
  .pager span{display:flex;align-items:center;justify-content:center;width:62px;height:26px;background:#111;color:var(--white);font-size:12px}
  .pager .prev{clip-path:polygon(14% 0,100% 0,100% 100%,14% 100%,0 50%)}
  .pager .next{clip-path:polygon(0 0,86% 0,100% 50%,86% 100%,0 100%)}

  /* products */
  .products{position:absolute;left:80px;top:1091px;width:1033px;display:grid;grid-template-columns:repeat(4,223px);justify-content:space-between;row-gap:51px}
  .product{position:relative;height:310px;border:1px solid var(--line);text-align:center}
  .product-photo{position:absolute;left:17px;top:20px;width:187px;height:170px}
  .product-name{position:absolute;top:199px;width:100%;font-size:16px;color:#333}
  .product-price{position:absolute;top:237px;width:100%;font-size:17px;font-weight:700;color:#222}
  .product-rating{position:absolute;top:266px;width:100%;font-size:12px;letter-spacing:1px;color:#aaa}

  /* footer */
  .site-footer{position:absolute;left:0;top:1837px;width:1200px;height:400px;background:radial-gradient(ellipse at 50% 40%,var(--footer) 0%,var(--footer-dark) 100%);color:var(--footer-text)}
  .footer-col{position:absolute;top:54px}
  .footer-col h3{font-size:26px;font-weight:300;color:var(--white);margin-bottom:22px}
  .about{left:80px;width:310px}
  .about p{font-size:13px;line-height:28px}
  .social{display:flex;gap:14px;margin-top:24px}
  .social span{width:44px;height:44px;border-radius:50%;background:var(--white)}
  .reach{left:510px}
  .reach li{list-style:none;position:relative;padding-left:38px;font-size:13px;line-height:29px;margin-bottom:8px}
  .reach svg{position:absolute;left:0;top:6px}
  .newsletter{left:824px;width:290px}
  .newsletter p{font-size:13px;line-height:29px}
  .signup{display:flex;margin-top:18px}
  .signup span{width:200px;height:40px;background:#e9e9e9}
  .signup b{width:87px;height:40px;background:var(--submit);color:var(--white);font-size:17px;display:flex;align-items:center;justify-content:center}
  .footer-rule{position:absolute;left:80px;top:305px;width:1033px;height:1px;background:#666}
  .footer-links{position:absolute;left:84px;top:343px;font-size:14px}
  .copyright{position:absolute;right:90px;top:343px;font-size:14px}
</style>
</head>
<body>

<header>
  <div class="topbar">
    <nav class="account-links"><a href="#">Register</a><span>|</span><a href="#">Login</a><span>|</span><a href="#">My Account</a></nav>
    <div class="search">Search
      <svg width="14" height="14" viewBox="0 0 14 14"><circle cx="5.5" cy="5.5" r="4.2" fill="none" stroke="#777" stroke-width="1.6"/><line x1="8.6" y1="8.6" x2="13" y2="13" stroke="#777" stroke-width="1.8"/></svg>
    </div>
    <div class="cart">
      <svg width="24" height="20" viewBox="0 0 24 20"><path d="M1 2h4l3 11h11l3-8H7" fill="none" stroke="#333" stroke-width="2"/><circle cx="9" cy="17" r="1.8" fill="#333"/><circle cx="18" cy="17" r="1.8" fill="#333"/></svg>
      Items (0)
    </div>
  </div>

  <div class="brand"><span>BRISA</span><span class="brand-mark"></span><span>PETALS</span></div>

  <nav class="main-nav">
    <a href="#" style="width:125px" aria-label="Home"><svg width="24" height="20" viewBox="0 0 24 20"><path d="M12 1 1 10h3v9h6v-6h4v6h6v-9h3z" fill="#222"/></svg></a>
    <a href="#" style="width:145px">Our Shop</a>
    <a href="#" style="width:214px">Fresh This Week</a>
    <a href="#" style="width:262px">Curated Collections</a>
    <a href="#" style="width:109px">Blog</a>
    <a href="#" style="width:178px">Contact Us</a>
  </nav>
</header>

<main>
  <section class="hero">
    <div class="hero-photo" role="img" aria-label="Bouquet of yellow roses lying on a rustic wooden table"></div>
    <div class="hero-copy">
      <p class="hero-kicker">CONSEQUAT IPMING</p>
      <svg class="hero-divider" viewBox="0 0 226 12"><line x1="0" y1="6" x2="95" y2="6" stroke="#fff"/><line x1="131" y1="6" x2="226" y2="6" stroke="#fff"/><path d="M109 2l8 8M117 2l-8 8" stroke="#fff" stroke-width="1.3"/></svg>
      <h1 class="hero-title">OFFER OF THE WEEK</h1>
      <p class="hero-text">Claritas est etiam processus dynamicus, qui sequitur mutationem consuetudium lectorum. Mirum est notare quam littera gothica, quam nunc</p>
      <a class="hero-button" href="#">SHOP NOW</a>
    </div>
    <svg class="hero-arrow prev" width="40" height="74" viewBox="0 0 40 74"><path d="M0 0 40 37 0 74z" fill="#fff"/><path d="M14 29l-7 8 7 8" fill="none" stroke="#333" stroke-width="1.6"/></svg>
    <svg class="hero-arrow next" width="40" height="74" viewBox="0 0 40 74"><path d="M40 0 0 37 40 74z" fill="#fff"/><path d="M26 29l7 8-7 8" fill="none" stroke="#333" stroke-width="1.6"/></svg>
  </section>

  <section>
    <h2 class="welcome-title">Welcome to<br>our <em>online store</em></h2>
    <p class="welcome-text">Duis autem vel eum iriure dolor in hendrerit in vulputate velit esse molestie consequat, vel illum dolore eu feugiat nulla facilisis at vero eros et accumsan et iusto. Nam liber tempor cum soluta nobis eleifend option congue nihil imperdiet doming. Nam liber tempor cum soluta nobis eleifend option congue nihil imperdiet.</p>
  </section>

  <section>
    <div class="tabs">
      <span class="rule"></span><span class="dot"></span>
      <span class="tab">Fresh This Week</span><span class="dot"></span>
      <span class="tab inactive">Curated Collections</span><span class="dot"></span>
      <span class="rule"></span>
    </div>
    <div class="pager"><span class="prev">prev</span><span class="next">next</span></div>

    <div class="products">
      <article class="product"><div class="product-photo" role="img" aria-label="Daisies and pink blooms in a polka-dot box" style="background:radial-gradient(circle at 50% 40%,#e45a7c,#f3e7ea 70%,#fbf7f8)"></div><p class="product-name">Beciegast nveriti vaert</p><p class="product-price">$119.50</p><p class="product-rating">☆☆☆☆☆</p></article>
      <article class="product"><div class="product-photo" role="img" aria-label="Yellow lilies and orange roses in a glass vase" style="background:radial-gradient(circle at 50% 40%,#e7c43a,#f4efd9 70%,#fbfaf5)"></div><p class="product-name">Beciegast nveriti vaert</p><p class="product-price">$119.50</p><p class="product-rating">☆☆☆☆☆</p></article>
      <article class="product"><div class="product-photo" role="img" aria-label="Pink lilies and magenta roses in a square vase" style="background:radial-gradient(circle at 50% 40%,#d4447a,#f3e4ec 70%,#fbf7f9)"></div><p class="product-name">Beciegast nveriti vaert</p><p class="product-price">$119.50</p><p class="product-rating">☆☆☆☆☆</p></article>
      <article class="product"><div class="product-photo" role="img" aria-label="Yellow roses and purple flowers in a glass vase" style="background:radial-gradient(circle at 50% 40%,#b7a23a,#ece8e2 70%,#fbfaf8)"></div><p class="product-name">Beciegast nveriti vaert</p><p class="product-price">$119.50</p><p class="product-rating">☆☆☆☆☆</p></article>
      <article class="product"><div class="product-photo" role="img" aria-label="Purple roses and green chrysanthemums in a violet cube" style="background:radial-gradient(circle at 50% 40%,#9a6aa8,#ebe6ee 70%,#faf9fb)"></div><p class="product-name">Beciegast nveriti vaert</p><p class="product-price">$119.50</p><p class="product-rating">☆☆☆☆☆</p></article>
      <article class="product"><div class="product-photo" role="img" aria-label="Pink roses and lavender blooms in a glass vase" style="background:radial-gradient(circle at 50% 40%,#d99ac0,#f1e8f0 70%,#fbf9fb)"></div><p class="product-name">Beciegast nveriti vaert</p><p class="product-price">$119.50</p><p class="product-rating">☆☆☆☆☆</p></article>
      <article class="product"><div class="product-photo" role="img" aria-label="Mixed orange and red lilies in a tall vase" style="background:radial-gradient(circle at 50% 40%,#e07a3a,#f3e9df 70%,#fbf8f5)"></div><p class="product-name">Beciegast nveriti vaert</p><p class="product-price">$119.50</p><p class="product-rating">☆☆☆☆☆</p></article>
      <article class="product"><div class="product-photo" role="img" aria-label="Yellow lilies and pink blooms in a pink vase" style="background:radial-gradient(circle at 50% 40%,#e8c03c,#f4ebe4 70%,#fbf9f6)"></div><p class="product-name">Beciegast nveriti vaert</p><p class="product-price">$119.50</p><p class="product-rating">☆☆☆☆☆</p></article>
    </div>
  </section>
</main>

<footer class="site-footer">
  <div class="footer-col about">
    <h3>Meet Brisa</h3>
    <p>Based in Marisol Heights, Bahia Vista - We offer farm fresh, curated, cool, and same day delivery flower bouquets. miuagtarsa nerafae kertyerauas.</p>
    <div class="social" aria-label="Social links"><span></span><span></span><span></span></div>
  </div>
  <div class="footer-col reach">
    <h3>Reach Brisa</h3>
    <ul>
      <li><svg width="16" height="20" viewBox="0 0 16 20"><path d="M8 0a7 7 0 0 0-7 7c0 5 7 13 7 13s7-8 7-13a7 7 0 0 0-7-7zm0 10a3 3 0 1 1 0-6 3 3 0 0 1 0 6z" fill="#fff"/></svg>2210 Marigold Avenue<br>Bahia Vista, CA 90999</li>
      <li><svg width="20" height="14" viewBox="0 0 20 14"><rect x="0" y="0" width="20" height="14" fill="#fff"/><path d="M0 0l10 8 10-8" fill="none" stroke="#333" stroke-width="1.5"/></svg>info@brisapetals.example</li>
      <li><svg width="18" height="18" viewBox="0 0 18 18"><path d="M4 1l3 4-2 2c1 3 3 5 6 6l2-2 4 3-2 3C8 17 1 10 1 3z" fill="#fff"/></svg>619-555-0148</li>
    </ul>
  </div>
  <div class="footer-col newsletter">
    <h3>Newsletter</h3>
    <p>We promise to only send you good things like discounts!</p>
    <div class="signup"><span></span><b>SUBMIT</b></div>
  </div>
  <div class="footer-rule"></div>
  <nav class="footer-links"><a href="#">Terms and Conditions</a> | <a href="#">Privacy Policy</a> | <a href="#">Site Map</a></nav>
  <p class="copyright">Copyright © 2013. All Rights Reserved.</p>
</footer>

</body>
</html>
```